Whitcombe Business Card Design

The name of the business is Dario Whitcombe, CPA LLC
The service that we offer is Accounting, Tax & Consulting Services. I need it to have the following items:
Dario Whitcombe, Principal
Phone Number
Email Address
Physical Address

I have attached the company logo, one in black and one in white. Please provide a design in black background and the other in white background. Please include "Accounting, Tax & Consulting Services". I want the business card to be clean and very professional.

```html
<!DOCTYPE html>
<html lang="en">
<head>
<meta charset="utf-8">
<title>Dario Whitcombe, CPA LLC – Business Cards</title>
<link href="https://fonts.googleapis.com/css2?family=Montserrat:wght@500;600;700&family=Roboto:wght@300;400&display=swap" rel="stylesheet">
<style>
  :root {
    --backdrop: #2b2b2b;
    --card: #ececec;
    --ink: #3a3a3c;
    --ink-soft: #7a7a7c;
    --accent: #8e1a1f;
    --band-grey: #8d8d90;
  }
  * { margin: 0; padding: 0; box-sizing: border-box; }
  html, body { width: 1200px; height: 1138px; overflow: hidden; }
  body { background: var(--backdrop); position: relative; font-family: "Roboto", sans-serif; }

  .card {
    position: absolute;
    width: 622px;
    height: 375px;
    background: var(--card);
    border-radius: 16px;
    overflow: hidden;
    color: var(--ink);
  }
  .card--front { left: 272px; top: 184px; }
  .card--back { left: 274px; top: 606px; }

  .firm-name {
    font-family: "Montserrat", sans-serif;
    font-weight: 600;
    color: var(--ink);
    white-space: nowrap;
    letter-spacing: 0.3px;
  }
  .firm-title {
    font-family: "Montserrat", sans-serif;
    font-weight: 600;
    color: var(--ink-soft);
    letter-spacing: 2.4px;
    white-space: nowrap;
  }

  .card--front .firm-block {
    position: absolute;
    top: 198px;
    left: 0;
    width: 100%;
    text-align: center;
  }
  .card--front .firm-name { font-size: 26px; line-height: 30px; }
  .card--front .firm-title { font-size: 18px; line-height: 22px; margin-top: 1px; }

  .services {
    position: absolute;
    top: 326px;
    width: 100%;
    text-align: center;
    font-size: 16px;
    color: #2a2a2a;
  }
  .base-band {
    position: absolute;
    left: 0; bottom: 0;
    width: 100%;
    height: 8px;
    display: flex;
  }
  .base-band span { flex: 1; }
  .base-band .band-accent { background: var(--accent); }
  .base-band .band-grey { background: var(--band-grey); }

  .card--back .firm-block { position: absolute; top: 50px; left: 37px; }
  .card--back .firm-name { font-size: 21px; line-height: 24px; }
  .card--back .firm-title { font-size: 15px; line-height: 18px; letter-spacing: 2px; }

  .contact {
    position: absolute;
    right: 37px;
    top: 150px;
    text-align: right;
  }
  .person-name {
    font-family: "Montserrat", sans-serif;
    font-weight: 700;
    font-size: 21px;
    color: var(--accent);
    letter-spacing: 0.4px;
    line-height: 26px;
  }
  .person-role { font-size: 16px; font-weight: 300; line-height: 20px; }
  .address { margin-top: 26px; font-size: 16px; font-weight: 300; line-height: 24px; }
  .contact-list { list-style: none; margin-top: 3px; }
  .contact-list li {
    font-size: 16px;
    font-weight: 300;
    line-height: 24px;
    display: flex;
    justify-content: flex-end;
    align-items: center;
    gap: 9px;
  }
  .contact-list svg { width: 14px; height: 14px; fill: var(--accent); }
</style>
</head>
<body>

<section class="card card--front" aria-label="Business card front">
  <div class="firm-block">
    <div class="firm-name">DARIO WHITCOMBE, CPA, LLC</div>
    <div class="firm-title">CERTIFIED PUBLIC ACCOUNTANT</div>
  </div>
  <p class="services">Accounting, Tax &amp; Consulting Services</p>
  <div class="base-band"><span class="band-accent"></span><span class="band-grey"></span></div>
</section>

<section class="card card--back" aria-label="Business card back">
  <div class="firm-block">
    <div class="firm-name">DARIO WHITCOMBE, CPA, LLC</div>
    <div class="firm-title">CERTIFIED PUBLIC ACCOUNTANT</div>
  </div>

  <div class="contact">
    <div class="person-name">DARIO WHITCOMBE</div>
    <div class="person-role">Principal</div>
    <p class="address">5678, Harbor Lane, Elm City,<br>Elm County, US 204817</p>
    <ul class="contact-list">
      <li>555-204-7318
        <svg viewBox="0 0 16 16" aria-hidden="true"><path d="M1 6c0-2 3-4 7-4s7 2 7 4v1h-4V5.5H5V7H1z"/><path d="M3 8h10l1 6H2z"/></svg>
      </li>
      <li>dw@whitcombecpa.com
        <svg viewBox="0 0 16 16" aria-hidden="true"><path d="M1 3h14v10H1z M2.5 4.5 8 9l5.5-4.5" fill="none" stroke="#8e1a1f" stroke-width="1.6"/><path d="M1 3h14L8 8.6z"/></svg>
      </li>
      <li>www.whitcombecpa.com
        <svg viewBox="0 0 16 16" aria-hidden="true"><circle cx="8" cy="8" r="6.5" fill="none" stroke="#8e1a1f" stroke-width="1.6"/><path d="M1.5 8h13M8 1.5v13" stroke="#8e1a1f" stroke-width="1.3"/><ellipse cx="8" cy="8" rx="3" ry="6.5" fill="none" stroke="#8e1a1f" stroke-width="1.3"/></svg>
      </li>
    </ul>
  </div>
</section>

</body>
</html>
```